Building company buisness cards

We are looking for a sharp modern new look for our business cards.We are a New Zealand based company that specialises in house and land packages.We have attached a photo of the current logo and would like to see if it can be improved somehow if needed.We are open to any colours but we have chosen Black and White at this stage. Feel free to change the font and make the logo smarter looking.Play with the colours and see what looks best.We want a card that looks so good know one will want to throw it away!

Target Market(s)

Building profesonals, home buyers

Industry/Entity Type

Building

Contact Information for Business Card

Garrick Tenwood
0275390628
garrickt@hartvale.co.nz

Font styles to use
Serif
Sans Serif

Colors

Designer to choose colors to be used in the design.

Requirements
Must have
• Just the logo on one side and details on the other
• Clean simple looking card
Nice to have
• Round corners and detail like raised or spot UV
• Something that stands out
Should not have
• To title needed, Director etc

```html
<!DOCTYPE html>
<html lang="en">
<head>
<meta charset="utf-8">
<title>Hartvale Business Cards</title>
<link rel="stylesheet" href="https://fonts.googleapis.com/css2?family=Roboto+Slab:wght@700&family=Roboto:wght@400&display=swap">
<style>
  :root {
    --stage: #e9e9ea;
    --ink: #111111;
    --card-dark: #1f2124;
    --card-dark-edge: #2b2e32;
    --foil: #9a9c9f;
    --paper: #ffffff;
    --ghost: #ececec;
    --text: #1a1a1a;
  }
  * { margin: 0; padding: 0; box-sizing: border-box; }
  html, body { width: 1200px; height: 800px; overflow: hidden; }
  body {
    background: var(--stage);
    position: relative;
    font-family: "Roboto", Arial, sans-serif;
  }
  .card {
    position: absolute;
    top: 250px;
    width: 530px;
    height: 300px;
    border-radius: 22px;
    overflow: hidden;
    box-shadow: 0 10px 30px rgba(0,0,0,0.18);
  }
  .card--front {
    left: 40px;
    background: linear-gradient(135deg, var(--card-dark-edge), var(--card-dark));
    display: flex;
    align-items: center;
    justify-content: center;
    gap: 18px;
  }
  .front-wordmark {
    font-family: "Roboto Slab", Georgia, serif;
    font-weight: 700;
    font-size: 70px;
    color: var(--foil);
    letter-spacing: 1px;
  }
  .front-ring {
    width: 58px; height: 58px;
    border: 3px solid var(--foil);
    border-radius: 50%;
  }
  .card--back { left: 630px; background: var(--paper); }
  .back-art { position: absolute; inset: 0; }
  .brand-name {
    position: absolute;
    left: 14px; top: 196px;
    width: 126px;
    text-align: center;
    font-family: "Roboto Slab", Georgia, serif;
    font-weight: 700;
    font-size: 20px;
    color: var(--paper);
  }
  .contact {
    position: absolute;
    left: 245px; top: 84px;
    color: var(--text);
  }
  .contact-name {
    font-family: "Roboto Slab", Georgia, serif;
    font-weight: 700;
    font-size: 20px;
    padding-bottom: 8px;
    border-bottom: 1.5px solid var(--ink);
    width: 225px;
    margin-bottom: 14px;
  }
  .contact-line {
    display: flex;
    align-items: center;
    gap: 8px;
    font-size: 15px;
    margin-bottom: 8px;
  }
  .contact-line svg { flex: none; }
</style>
</head>
<body>
  <section class="card card--front" aria-label="Card front">
    <span class="front-wordmark">Hartvale</span>
    <span class="front-ring"></span>
  </section>

  <section class="card card--back" aria-label="Card back">
    <svg class="back-art" width="530" height="300" viewBox="0 0 530 300" aria-hidden="true">
      <circle class="ghost-ring" cx="430" cy="110" r="150" fill="none" stroke="var(--ghost)" stroke-width="10"/>
      <path class="corner-block" d="M0 170 H140 V300 H0 Z" fill="var(--ink)"/>
      <path class="corner-strip" d="M140 262 H0 V300 H140 Z" fill="var(--ink)"/>
      <circle class="brand-ring" cx="88" cy="124" r="44" fill="var(--paper)" stroke="var(--ink)" stroke-width="4"/>
      <line class="divider" x1="212" y1="80" x2="212" y2="210" stroke="var(--ink)" stroke-width="1.5"/>
    </svg>
    <div class="brand-name">Hartvale</div>

    <div class="contact">
      <p class="contact-name">Garrick Tenwood</p>
      <p class="contact-line">
        <svg width="16" height="16" viewBox="0 0 16 16" aria-hidden="true">
          <circle cx="8" cy="8" r="7" fill="none" stroke="var(--ink)" stroke-width="1.3"/>
          <rect x="5.5" y="3.8" width="5" height="8.4" rx="1" fill="none" stroke="var(--ink)" stroke-width="1.2"/>
        </svg>
        <span>0275390628</span>
      </p>
      <p class="contact-line">
        <svg width="16" height="16" viewBox="0 0 16 16" aria-hidden="true">
          <circle cx="8" cy="8" r="7.5" fill="var(--ink)"/>
          <rect x="4" y="5.2" width="8" height="5.6" fill="var(--paper)"/>
          <path d="M4 5.2 L8 8.6 L12 5.2" fill="none" stroke="var(--ink)" stroke-width="1"/>
        </svg>
        <span>garrickt@hartvale.co.nz</span>
      </p>
    </div>
  </section>
</body>
</html>
```